Webdesign für Personalvermittlung
Zielgruppe
Personalvermittlung
Aufgabenstellung
es soll einladend - nicht zu überladen und natürlich cool und modern sein

```html
<!DOCTYPE html>
<html lang="de">
<head>
<meta charset="utf-8">
<title>pflegeweg karriere – Dein nächster Schritt im Pflegeberuf</title>
<link rel="stylesheet" href="https://fonts.googleapis.com/css2?family=Merriweather+Sans:wght@400;700;800&family=Montserrat:wght@400;500;600&display=swap">
<style>
  :root {
    --white: #ffffff;
    --header-bg: #f7f7f7;
    --ink: #2b2b2b;
    --nav-active: #5b9be0;
    --contact-blue: #5b9be0;
    --accent-orange: #e58f3c;
    --photo-warm: #d9cbbb;
    --photo-light: #ece6de;
    --photo-blue: #5a8fc8;
    --shade: rgba(30, 26, 24, 0.55);
  }
  * { margin: 0; padding: 0; box-sizing: border-box; }
  html, body {
    width: 1200px;
    height: 800px;
    overflow: hidden;
    background: var(--white);
    font-family: "Merriweather Sans", sans-serif;
    color: var(--ink);
  }
  .page {
    position: relative;
    width: 1200px;
    height: 800px;
  }
  .site-header {
    position: absolute;
    inset: 0 0 auto 0;
    height: 104px;
    background: var(--header-bg);
    display: flex;
    align-items: center;
    justify-content: flex-end;
    padding-right: 90px;
    z-index: 3;
  }
  .brand-tab {
    position: absolute;
    left: 70px;
    top: 0;
    width: 230px;
    height: 150px;
    background: var(--header-bg);
    display: flex;
    flex-direction: column;
    align-items: center;
    justify-content: center;
    gap: 14px;
    z-index: 4;
  }
  .brand-dot {
    width: 58px;
    height: 58px;
    border-radius: 50%;
    background: var(--nav-active);
  }
  .brand-name {
    font-family: "Montserrat", sans-serif;
    font-weight: 500;
    font-size: 26px;
    color: var(--ink);
    letter-spacing: 0.2px;
  }
  .main-nav {
    display: flex;
    align-items: center;
    gap: 22px;
    font-family: "Montserrat", sans-serif;
    font-weight: 500;
    font-size: 18px;
  }
  .main-nav a { color: var(--ink); text-decoration: none; }
  .main-nav a.is-active { color: var(--nav-active); }
  .main-nav a.nav-contact {
    background: var(--contact-blue);
    color: var(--white);
    padding: 11px 20px;
    border-radius: 3px;
    margin-left: 8px;
  }
  .hero {
    position: absolute;
    inset: 104px 0 0 0;
    overflow: hidden;
  }
  .hero-photo {
    position: absolute;
    inset: 0;
    background:
      radial-gradient(ellipse 320px 420px at 74% 62%, var(--photo-blue) 0%, rgba(90,143,200,0.6) 45%, rgba(90,143,200,0) 75%),
      radial-gradient(ellipse 180px 160px at 71% 28%, #c98a64 0%, rgba(201,138,100,0) 80%),
      linear-gradient(100deg, var(--photo-warm) 0%, var(--photo-light) 45%, #e4dcd2 100%);
  }
  .hero-shade {
    position: absolute;
    inset: 0;
    background: linear-gradient(12deg, var(--shade) 0%, rgba(30,26,24,0.25) 40%, rgba(30,26,24,0) 65%);
  }
  .hero-copy {
    position: absolute;
    left: 90px;
    bottom: 90px;
    width: 640px;
    color: var(--white);
  }
  .hero-title {
    font-weight: 800;
    font-size: 52px;
    line-height: 1.15;
    margin-bottom: 24px;
  }
  .hero-lead {
    font-weight: 400;
    font-size: 17px;
    line-height: 1.55;
    margin-bottom: 30px;
  }
  .hero-lead strong { font-weight: 700; }
  .hero-actions { display: flex; gap: 18px; }
  .btn {
    font-family: "Merriweather Sans", sans-serif;
    font-size: 15px;
    padding: 13px 26px;
    border-radius: 2px;
    text-decoration: none;
    color: var(--white);
  }
  .btn-primary { background: var(--accent-orange); }
  .btn-outline { border: 1.5px solid var(--white); }
</style>
</head>
<body>
<div class="page">
  <header class="site-header">
    <div class="brand-tab">
      <span class="brand-dot"></span>
      <span class="brand-name">pflegeweg karriere</span>
    </div>
    <nav class="main-nav">
      <a class="is-active" href="#">Home</a>
      <a href="#">Wir bieten dir</a>
      <a href="#">Über uns</a>
      <a class="nav-contact" href="#">Kontakt</a>
    </nav>
  </header>

  <section class="hero">
    <div class="hero-photo" role="img" aria-label="Foto: lächelnde Pflegekraft in blauer Dienstkleidung mit Stethoskop, im Hintergrund ein älterer Bewohner in einem hellen Zimmer"></div>
    <div class="hero-shade"></div>
    <div class="hero-copy">
      <h1 class="hero-title">Dein nächster Schritt<br>im Pflegeberuf!</h1>
      <p class="hero-lead">Willkommen bei <strong>pflegeweg-karriere.de</strong>! Mit über 15 Jahren Erfahrung sind wir dein vertrauensvoller Partner für die nächsten Stufe deiner Karriere.</p>
      <div class="hero-actions">
        <a class="btn btn-primary" href="#">Was wir dir bieten</a>
        <a class="btn btn-outline" href="#">Angebot anfordern</a>
      </div>
    </div>
  </section>
</div>
</body>
</html>
```